Business Cards for IT Consulting Company (Managed Service Provider)

I am looking to have some business cards printed and would like some designs. We are an IT Consulting company based in Vancouver BC. I would like a nice clean and modern look to the cards. I have uploaded all the versions of my logo so parts can be used as needed. Here is a snippit from our website homepage:

Quillbrook Networks Ltd. is an IT Solutions Partner located in Vancouver BC, Canada. We offer IT solutions and support to customers in the greater Vancouver Area. With expertise in Microsoft platforms, as well as Linux and Mac OSX and over 12 years experience in the IT industry, Quillbrook Networks is dedicated to offering our clients top quality service and products. We take pride in the solutions we offer our customers. The greatest compliment a client can give us is to recommend our services.

Quillbrook Networks Ltd. offers a wide range of IT services from onsite service to remote support and managed service solutions. This allows clients to choose the support path that best suits their company’s needs. Supporting many different sized companies from small to enterprise level over the past 12 years Quillbrook Networks has the experience and expertise needed to ensure things run smoothly. Allowing our clients to focus on doing business.

Revolutionizing the way IT services are delivered.

Quillbrook Networks is dedicated to providing our clients with IT solutions that work and grow with them for years to come. This philosophy helps save money in the long run instead of replacing equipment constantly. Far too often IT solutions are not well thought out and while possibly solving the problem at hand, require replacement due to growth or quality within a very short time frame. Quillbrook Networks takes pride in providing solutions that will last and be able to accommodate growth without the need for replacement.

Industry/Entity Type

Information Technology

Contact Information for Business Card

Quillbrook Networks Ltd.
(Employee Name)
Eml: (Employees Email Address)
Web: quillbrook.me
Ph: 604-555-0148

Font styles to use
Serif
Sans Serif

Requirements
Must have
• The Company logo and company colors.
Nice to have
• - Our tag line: "Revolutionizing IT Services" or "Revolutionizing the way IT services are delivered."
• - Also I really like the idea of nature and technology together blending which is sort of where my logo came from so integrating that somehow onto the business cards would be great.

```html
<!DOCTYPE html>
<html lang="en">
<head>
<meta charset="utf-8">
<title>Quillbrook Networks Ltd. – Business Cards</title>
<link rel="stylesheet" href="https://fonts.googleapis.com/css2?family=Montserrat:wght@600&family=Arimo:wght@400;700&display=swap">
<style>
  :root {
    --page-bg: #e9e7e3;
    --card-back: #6b6c6e;
    --card-back-dark: #58595b;
    --card-front: #ffffff;
    --brand-blue: #29abe2;
    --brand-gray: #6d6e71;
    --ink-white: #ffffff;
  }
  * { box-sizing: border-box; margin: 0; padding: 0; }
  html, body { width: 1200px; height: 950px; overflow: hidden; }
  body {
    background: var(--page-bg);
    display: flex;
    flex-direction: column;
    align-items: center;
    justify-content: center;
    gap: 50px;
    font-family: "Arimo", Arial, sans-serif;
  }
  .card {
    position: relative;
    width: 700px;
    height: 400px;
    border-radius: 4px;
    overflow: hidden;
    box-shadow: 0 6px 18px rgba(0,0,0,0.18);
  }

  /* Back side */
  .card-back {
    background: linear-gradient(135deg, var(--card-back) 0%, var(--card-back-dark) 100%);
    display: flex;
    flex-direction: column;
    align-items: center;
    justify-content: center;
    color: var(--ink-white);
  }
  .brand {
    display: flex;
    align-items: center;
    gap: 18px;
    font-family: "Montserrat", sans-serif;
    font-weight: 600;
  }
  .brand-mark {
    width: 46px;
    height: 46px;
    border: 3px solid currentColor;
  }
  .brand-name { line-height: 1; }
  .brand-name .primary { display: block; font-size: 58px; letter-spacing: 0.5px; }
  .brand-name .secondary { display: block; font-size: 21px; letter-spacing: 3px; margin-top: 4px; text-transform: uppercase; }
  .tagline {
    margin-top: 44px;
    font-size: 17px;
    letter-spacing: 0.3px;
  }

  /* Front side */
  .card-front { background: var(--card-front); }
  .card-front .shapes { position: absolute; inset: 0; }
  .card-front .brand {
    position: absolute;
    left: 150px;
    top: 96px;
    color: var(--brand-blue);
  }
  .contact {
    position: absolute;
    right: 34px;
    top: 268px;
    color: var(--ink-white);
    font-size: 17px;
    line-height: 30px;
    text-align: right;
  }
  .contact-row {
    display: flex;
    align-items: center;
    justify-content: flex-end;
    gap: 10px;
  }
  .contact-row svg { width: 16px; height: 16px; fill: var(--ink-white); }
  .holder {
    position: absolute;
    left: 34px;
    top: 318px;
    color: var(--ink-white);
    font-size: 17px;
    line-height: 23px;
  }
  .holder-name { font-weight: 700; font-size: 19px; margin-bottom: 2px; }
</style>
</head>
<body>

  <section class="card card-back" aria-label="Card back">
    <div class="brand">
      <span class="brand-mark"></span>
      <span class="brand-name">
        <span class="primary">Quillbrook</span>
        <span class="secondary">Networks Ltd.</span>
      </span>
    </div>
    <p class="tagline">Revolutionizing IT Services</p>
  </section>

  <section class="card card-front" aria-label="Card front">
    <svg class="shapes" viewBox="0 0 700 400" preserveAspectRatio="none">
      <path d="M0 300 L330 300 L362 250 L700 250 L700 400 L0 400 Z" fill="var(--brand-blue)"/>
      <path d="M0 285 L322 285 L354 236 L374 236 L342 300 L0 300 Z" fill="var(--brand-gray)"/>
    </svg>

    <div class="brand">
      <span class="brand-mark"></span>
      <span class="brand-name">
        <span class="primary">Quillbrook</span>
        <span class="secondary">Networks Ltd.</span>
      </span>
    </div>

    <div class="contact">
      <div class="contact-row">
        <span>576 555 0193</span>
        <svg viewBox="0 0 16 16" aria-hidden="true"><path d="M3.6 1.2 6 3.8 4.8 5.6c.9 2 2.6 3.7 4.6 4.6l1.8-1.2 2.6 2.4-1.4 2.2C7 13.4 2.6 9 1.4 2.6Z"/></svg>
      </div>
      <div class="contact-row">
        <span>mara@quillbrook.me</span>
        <svg viewBox="0 0 16 16" aria-hidden="true"><path d="M1 3h14v1.2L8 9 1 4.2Z M1 5.8 8 10.6l7-4.8V13H1Z"/></svg>
      </div>
      <div class="contact-row">
        <span>www.quillbrook.me</span>
        <svg viewBox="0 0 16 16" aria-hidden="true"><circle cx="8" cy="8" r="6.5" fill="none" stroke="#fff" stroke-width="1.6"/><path d="M1.5 8h13M8 1.5c-3 3.5-3 9.5 0 13M8 1.5c3 3.5 3 9.5 0 13" fill="none" stroke="#fff" stroke-width="1.2"/></svg>
      </div>
    </div>

    <div class="holder">
      <p class="holder-name">Mara Lintell</p>
      <p>2718 Alder Crescent</p>
      <p>Burnaby, BC V5A 1K3</p>
    </div>
  </section>

</body>
</html>
```